Corporate Business Card

Very professional, Modern, Not to busy, include phone address email, website
(253) 617-4930, 18761 52nd Avenue S, Kent, WA 98047, martin@plumlinegroup.com, varkoworks.com

Target Market(s)

Manufacturing

Industry/Entity Type

Aero, machining, manufacturing, Off road racing

Contact Information for Business Card

Phone, address email, website

```html
<!DOCTYPE html>
<html lang="en">
<head>
<meta charset="utf-8">
<title>Varko Works – Business Card</title>
<link href="https://fonts.googleapis.com/css2?family=Exo+2:wght@600;700&family=Montserrat:wght@400&display=swap" rel="stylesheet">
<style>
  :root {
    --backdrop: #6e5c47;
    --navy: #20356b;
    --red: #c8191e;
    --white: #ffffff;
    --ink: #333333;
  }
  * { margin: 0; padding: 0; box-sizing: border-box; }
  html, body { width: 900px; height: 1200px; overflow: hidden; }
  body { background: var(--backdrop); position: relative; font-family: "Montserrat", sans-serif; }

  .card {
    position: absolute;
    left: 80px;
    width: 742px;
    height: 440px;
    border-radius: 30px;
  }
  .card--front { top: 132px; background: var(--navy); }
  .card--back { top: 638px; background: var(--white); }

  .brand-name {
    position: absolute;
    left: 0; right: 0;
    text-align: center;
    font-family: "Exo 2", sans-serif;
    font-weight: 700;
    font-size: 86px;
    letter-spacing: 1px;
    line-height: 1;
  }
  .card--front .brand-name { top: 172px; color: var(--white); }
  .card--back .brand-name { top: 100px; color: var(--navy); }

  .holder {
    position: absolute;
    right: 422px;
    top: 308px;
    text-align: right;
    color: var(--ink);
    font-size: 16px;
    line-height: 23px;
  }
  .holder__name {
    font-family: "Exo 2", sans-serif;
    font-weight: 600;
    font-size: 28px;
    line-height: 32px;
    color: var(--red);
    letter-spacing: 0.5px;
  }
  .divider {
    position: absolute;
    left: 352px;
    top: 317px;
    width: 2px;
    height: 63px;
    background: var(--red);
  }
  .contact {
    position: absolute;
    left: 392px;
    top: 311px;
    list-style: none;
    color: var(--ink);
    font-size: 16px;
    line-height: 22.5px;
  }
  .contact li { display: flex; align-items: center; }
  .contact svg { width: 12px; height: 12px; margin-right: 13px; flex: none; }
</style>
</head>
<body>
  <section class="card card--front">
    <div class="brand-name">Varko Works</div>
  </section>

  <section class="card card--back">
    <div class="brand-name">Varko Works</div>

    <div class="holder">
      <div class="holder__name">Martin Kessler</div>
      <div class="holder__title">Managing Director</div>
      <div class="holder__address">52nd Avenue S, Kent, WA 98047</div>
    </div>

    <div class="divider"></div>

    <ul class="contact">
      <li>
        <svg viewBox="0 0 12 12" aria-hidden="true"><path fill="#c8191e" d="M1 4.5C1 3 3 2 6 2s5 1 5 2.5L9 5 8.5 3.8h-5L3 5zM3 6h6l1 4.5H2z"/></svg>
        (253) 617-4930, 18761
      </li>
      <li>
        <svg viewBox="0 0 12 12" aria-hidden="true"><path fill="#c8191e" d="M1 3h10v1.2L6 7 1 4.2zM1 5.4l5 2.8 5-2.8V10H1z"/></svg>
        martin@plumlinegroup.com
      </li>
      <li>
        <svg viewBox="0 0 12 12" aria-hidden="true"><circle cx="6" cy="6" r="5" fill="#c8191e"/><path fill="#fff" d="M3.5 4.5l2-1 1 1.5-1.5 1 .5 2-1.5-.5zM7.5 7l1.5-.5.3 1.5-1.3 1z"/></svg>
        www.varkoworks.com
      </li>
    </ul>
  </section>
</body>
</html>
```